Oil and Gas Exploration and Production company needs a business card design

We need a business card design using our logo and colors in the logo. We want a mainstream design.

```html
<!DOCTYPE html>
<html lang="en">
<head>
<meta charset="utf-8">
<title>Ridgeline Fuel – Business Card</title>
<link href="https://fonts.googleapis.com/css2?family=Arimo:wght@400;700&display=swap" rel="stylesheet">
<style>
  :root {
    --page-bg: #e9e6e1;
    --card-light: #f7f5f2;
    --card-mid: #ece7e0;
    --ink: #161616;
    --bronze: #a8671e;
    --bronze-light: #d49a4c;
    --band: #141414;
    --muted: #9a9a9a;
  }
  html, body {
    margin: 0;
    width: 1200px;
    height: 970px;
    overflow: hidden;
    background: var(--page-bg);
    font-family: "Arimo", Arial, sans-serif;
  }
  .canvas {
    position: relative;
    width: 1200px;
    height: 970px;
    display: flex;
    align-items: center;
    justify-content: center;
  }
  .business-card {
    position: relative;
    width: 880px;
    height: 500px;
    border-radius: 22px;
    overflow: hidden;
    background: linear-gradient(160deg, var(--card-light) 0%, var(--card-mid) 100%);
    box-shadow: 0 18px 40px rgba(0,0,0,0.18);
  }
  .brand {
    position: absolute;
    left: 74px;
    top: 212px;
    width: 336px;
    display: flex;
    align-items: center;
    gap: 12px;
    white-space: nowrap;
  }
  .brand-dot {
    width: 38px;
    height: 38px;
    flex: none;
    border-radius: 50%;
    background: var(--ink);
  }
  .brand-name {
    font-weight: 700;
    font-size: 36px;
    line-height: 1;
    color: var(--ink);
    letter-spacing: -0.5px;
  }
  .divider {
    position: absolute;
    left: 436px;
    top: 140px;
    width: 2px;
    height: 194px;
    background: var(--ink);
  }
  .contact {
    position: absolute;
    left: 474px;
    top: 126px;
    color: var(--ink);
    white-space: nowrap;
  }
  .person-name {
    margin: 0;
    font-weight: 700;
    font-size: 28px;
    line-height: 1;
  }
  .person-title {
    margin: 2px 0 0;
    font-size: 21px;
    color: var(--bronze);
  }
  .address {
    margin: 40px 0 0;
    font-size: 21px;
    line-height: 28px;
  }
  .contact-line {
    display: flex;
    align-items: center;
    gap: 14px;
    font-size: 21px;
    line-height: 27px;
  }
  .contact-line:first-of-type { margin-top: 10px; }
  .contact-line svg { width: 20px; height: 16px; flex: none; }
  .wave {
    position: absolute;
    left: 0;
    bottom: 0;
    width: 880px;
    height: 500px;
  }
  .website {
    position: absolute;
    right: 48px;
    bottom: 24px;
    font-size: 20px;
    letter-spacing: 2px;
    color: var(--muted);
  }
  .website .accent { color: var(--bronze); }
</style>
</head>
<body>
<main class="canvas">
  <section class="business-card">
    <svg class="wave" viewBox="0 0 880 500" aria-hidden="true">
      <defs>
        <linearGradient id="bronzeSwoosh" x1="0" x2="1" y1="0" y2="0">
          <stop offset="0" stop-color="#c08a4a" stop-opacity="0.3"/>
          <stop offset="0.5" stop-color="#9a5a18"/>
          <stop offset="1" stop-color="#d49a4c"/>
        </linearGradient>
      </defs>
      <path d="M0,398 C180,420 330,470 470,468 C620,466 760,405 880,392 L880,500 L0,500 Z" fill="var(--band)"/>
      <path d="M6,392 C190,420 330,462 470,458 C620,454 760,398 870,383 C760,392 620,440 470,446 C330,452 190,414 6,392 Z" fill="url(#bronzeSwoosh)"/>
    </svg>

    <div class="brand">
      <span class="brand-dot"></span>
      <span class="brand-name">Ridgeline Fuel</span>
    </div>

    <div class="divider"></div>

    <div class="contact">
      <h1 class="person-name">Daniel Reyes</h1>
      <p class="person-title">President &amp; CEO</p>
      <p class="address">PO BOX 480, Harbour Road<br>Dock Row, Leeds</p>
      <div class="contact-line">
        <svg viewBox="0 0 20 16" aria-hidden="true"><path d="M2,5 C2,2 18,2 18,5 L15,6 L14,4 L6,4 L5,6 Z M4,8 L16,8 L17,15 L3,15 Z" fill="var(--bronze)"/><circle cx="10" cy="11" r="2" fill="var(--card-light)"/></svg>
        <span>(123) 555 0142</span>
      </div>
      <div class="contact-line">
        <svg viewBox="0 0 20 16" aria-hidden="true"><rect x="1" y="2" width="18" height="12" fill="var(--bronze)"/><path d="M1,2 L10,9 L19,2 M1,14 L8,8 M19,14 L12,8" stroke="var(--card-light)" stroke-width="1.4" fill="none"/></svg>
        <span>hello@ridgelinefuel.com</span>
      </div>
    </div>

    <div class="website">www.<span class="accent">ridgelinefuel</span>.com</div>
  </section>
</main>
</body>
</html>
```